Website Design Request - Management Consulting Firm

We need a Website designed for an IT Management Staffing and Recruiting firm called TRAVENOK based in San Francisco.

The firm is an high-end technology staffing agency. Our focus is on quality and high-caliber candidates rather than quantity.

The website will have two main home pages. One for the recruiter and another on for the candidates.

The website needs to optimize for mobile devices as well.

I have attached few mock-ups that I have done just to show what I am thinking. The UI needs to be very clean, fluid, and it needs to have a modern, rustic, professional feel to it.

Target Market(s)

Technology Manager, Director, VP, CIO of Companies that have $4b-10b dollar revenue. Such as larkspurdwellings.example , https://www.velmorian.example/, quillnet.example, zib.example

Industry/Entity Type

Management Consulting

Number of Pages Required

5+ page

Font styles to use
Sans Serif

Colors
f37122
ffffff

Requirements
Must have
• Please review mock-ups for suggestions
Nice to have
Should not have

```html
<!DOCTYPE html>
<html lang="en">
<head>
<meta charset="utf-8">
<title>TRAVENOK – IT Project Management Jobs</title>
<link rel="stylesheet" href="https://fonts.googleapis.com/css2?family=Nunito+Sans:wght@300;400;600&display=swap">
<style>
  :root {
    --brand: #f37122;
    --brand-dark: #e8631a;
    --white: #ffffff;
    --ink: #333333;
    --ink-soft: #555555;
    --muted: #9a9a9a;
    --faint: #d9d9d9;
    --band: #c8c8c8;
    --footer-bg: #f2f2f2;
    --hero-a: #d9d9d9;
    --hero-b: #f1f1f1;
  }
  * { box-sizing: border-box; margin: 0; padding: 0; }
  html, body { width: 839px; height: 1200px; overflow: hidden; }
  body {
    position: relative;
    background: var(--white);
    font-family: "Nunito Sans", sans-serif;
    font-weight: 300;
    color: var(--ink);
  }
  .abs { position: absolute; }

  /* Header */
  .site-header { left: 0; top: 0; width: 839px; height: 64px; background: var(--white); }
  .brand { left: 100px; top: 15px; font-size: 29px; font-weight: 400; letter-spacing: 1px; color: var(--brand); line-height: 34px; }
  .main-nav a { position: absolute; top: 25px; font-size: 13px; color: var(--ink-soft); text-decoration: none; font-weight: 400; }

  /* Hero */
  .hero { left: 0; top: 64px; width: 839px; height: 338px;
    background: linear-gradient(100deg, var(--hero-a) 0%, var(--hero-b) 45%, var(--hero-b) 60%, var(--hero-a) 100%); }
  .hero-title { left: 0; width: 839px; top: 152px; text-align: center; font-size: 28px; font-weight: 400; color: var(--ink); }
  .hero-sub { left: 0; width: 839px; top: 188px; text-align: center; font-size: 17px; font-weight: 400; color: var(--ink); }
  .email-field { left: 244px; top: 224px; width: 338px; height: 31px; background: var(--white); border: 1px solid #cfcfcf;
    font-size: 10px; color: var(--muted); padding: 9px 14px; font-weight: 400; }
  .cta { left: 315px; top: 263px; width: 202px; height: 29px; background: linear-gradient(var(--brand), var(--brand-dark));
    color: var(--white); font-size: 12.5px; font-weight: 400; text-align: center; line-height: 29px; }
  .hero-note { left: 0; width: 839px; top: 305px; text-align: center; font-size: 10px; font-weight: 400; color: var(--ink); }
  .hero-note a { color: var(--ink); }
  .slider-dots { left: 391px; top: 377px; }
  .slider-dots span { position: absolute; top: 0; width: 9px; height: 9px; border-radius: 50%; background: var(--white); }
  .slider-dots span.is-current { background: transparent; border: 1px solid var(--white); }

  /* Tabs */
  .tab-band { left: 0; top: 402px; width: 839px; height: 35px; background: var(--band); }
  .tab { top: 402px; height: 35px; line-height: 35px; font-size: 16px; font-weight: 400; color: var(--white); text-align: center; }
  .tab-active { left: 260px; width: 162px; background: var(--brand); }
  .tab-arrow { left: 333px; top: 437px; width: 0; height: 0; border-left: 8px solid transparent; border-right: 8px solid transparent; border-top: 9px solid var(--brand); }
  .tab-other { left: 440px; width: 100px; }

  /* Steps */
  .section-kicker { left: 0; width: 839px; top: 479px; text-align: center; font-size: 13px; font-weight: 400; }
  .section-sub { left: 0; width: 839px; top: 505px; text-align: center; font-size: 14px; color: var(--muted); }
  .timeline-line { left: 348px; top: 603px; width: 2px; height: 222px; background: var(--faint); }
  .step-dot { width: 13px; height: 13px; border-radius: 50%; background: var(--faint); left: 342px; }
  .step-dot.is-current { background: var(--brand); }
  .step-num { left: 303px; font-size: 44px; font-weight: 300; color: #e6e6e6; line-height: 44px; }
  .step-title { left: 372px; font-size: 18px; font-weight: 400; color: var(--ink); }
  .step-text { left: 373px; font-size: 11px; line-height: 16.5px; color: var(--muted); font-weight: 400; }
  .step-icon { left: 188px; }

  .upload-btn { left: 322px; top: 906px; width: 184px; height: 40px; border: 1.5px solid var(--brand); border-radius: 20px;
    color: var(--brand); font-size: 13.5px; font-weight: 400; display: flex; align-items: center; justify-content: center; gap: 6px; }

  /* Footer */
  .site-footer { left: 0; top: 996px; width: 839px; height: 204px; background: var(--footer-bg); }
  .footer-col h3 { font-size: 15px; font-weight: 300; color: var(--ink-soft); margin-bottom: 6px; }
  .footer-col a { display: block; font-size: 8.5px; line-height: 16.5px; color: var(--muted); text-decoration: none; font-weight: 400; padding-left: 2px; }
  .social { top: 1057px; width: 24px; height: 24px; border-radius: 50%; background: var(--brand); }
  .footer-brand { left: 516px; top: 1092px; font-size: 38px; font-weight: 400; letter-spacing: 1px; color: #d4d4d4; }
  .copyright { left: 122px; top: 1159px; font-size: 8.5px; color: var(--muted); font-weight: 400; }
</style>
</head>
<body>

<header class="abs site-header">
  <div class="abs brand">TRAVENOK</div>
  <nav class="main-nav">
    <a href="#" style="left:437px">Professionals</a>
    <a href="#" style="left:538px">Employers</a>
    <a href="#" style="left:626px">Sign In</a>
    <a href="#" style="left:694px">Sign Up</a>
  </nav>
</header>

<section class="abs hero" role="img" aria-label="Photo of young professionals working at computers in a bright office, faded to a light grey"></section>
<h1 class="abs hero-title">Looking for IT Project Management Jobs?</h1>
<p class="abs hero-sub">Upload your resume, accept interview requests, get offer.</p>
<div class="abs email-field">Your Email address</div>
<div class="abs cta">Get Offers Now</div>
<p class="abs hero-note">Looking for talents? <a href="#">See how it works for Employers</a></p>
<div class="abs slider-dots">
  <span class="is-current" style="left:0"></span>
  <span style="left:16px"></span>
  <span style="left:32px"></span>
  <span style="left:47px"></span>
</div>

<div class="abs tab-band"></div>
<div class="abs tab tab-active">How it Works</div>
<div class="abs tab-arrow"></div>
<div class="abs tab tab-other">Why Us?</div>

<h2 class="abs section-kicker">3 Simple Steps</h2>
<p class="abs section-sub">Employers pay 25% more for a better FIT Project Manager</p>

<div class="abs timeline-line"></div>

<!-- Step 1 -->
<svg class="abs step-icon" style="top:572px" width="80" height="68" viewBox="0 0 80 68" fill="none" stroke="#f37122" stroke-width="2">
  <path d="M18 48 H12 A11 11 0 0 1 12 26 A14 14 0 0 1 30 14 A18 18 0 0 1 62 20 A13 13 0 0 1 66 48 H60"/>
  <circle cx="39" cy="50" r="15"/>
  <path d="M39 59 V42 M32 48 L39 41 L46 48"/>
</svg>
<div class="abs step-num" style="top:580px">1</div>
<div class="abs step-dot is-current" style="top:596px"></div>
<div class="abs step-title" style="top:584px">Upload your Resume</div>
<div class="abs step-text" style="top:612px">Answer few questions and upload your resume</div>

<!-- Step 2 -->
<svg class="abs step-icon" style="top:684px; left:202px" width="62" height="46" viewBox="0 0 62 46" fill="none" stroke="#f37122" stroke-width="2">
  <rect x="2" y="2" width="58" height="42" rx="2"/>
  <path d="M2 4 L31 27 L60 4 M2 43 L24 22 M60 43 L38 22"/>
</svg>
<div class="abs step-num" style="top:686px">2</div>
<div class="abs step-dot" style="top:702px"></div>
<div class="abs step-title" style="top:686px">We Send You Interview Requests</div>
<div class="abs step-text" style="top:713px">Interested in someone? With a single clic,<br>send interview request and let us handle the rest</div>

<!-- Step 3 -->
<svg class="abs step-icon" style="top:781px; left:196px" width="76" height="74" viewBox="0 0 76 74" fill="none" stroke="#f37122" stroke-width="2">
  <path d="M21 10 V14 M26 6 V14 M31 8 V14 M36 2 V14" stroke-linecap="round"/>
  <circle cx="30" cy="30" r="12" fill="#f37122"/>
  <text x="30" y="36" text-anchor="middle" font-family="Nunito Sans, sans-serif" font-size="16" font-weight="600" fill="#ffffff" stroke="none">$</text>
  <path d="M4 52 C14 50 22 56 30 58 L52 58 M4 52 C10 62 22 66 34 66 L52 66 M30 58 C36 56 40 52 44 50"/>
  <rect x="52" y="46" width="8" height="22" fill="#f37122"/>
  <path d="M60 70 H72"/>
</svg>
<div class="abs step-num" style="top:800px">3</div>
<div class="abs step-dot" style="top:818px"></div>
<div class="abs step-title" style="top:803px">Get $1000 Bonus</div>
<div class="abs step-text" style="top:832px">Find a Job and get $1000 bonus TRAVENOK</div>

<div class="abs upload-btn">
  <svg width="18" height="17" viewBox="0 0 18 17" fill="#f37122"><path d="M9 0 L15 6 H11 V12 H7 V6 H3 Z"/><path d="M1 10 H3 V14 H15 V10 H17 V16 H1 Z"/></svg>
  Upload Your Resume
</div>

<footer class="abs site-footer"></footer>
<div class="abs footer-col" style="left:122px; top:1028px">
  <h3>Company</h3>
  <a href="#">Home</a><a href="#">Why We Are</a><a href="#">About Us</a><a href="#">Our Team</a>
</div>
<div class="abs footer-col" style="left:248px; top:1028px">
  <h3>Sublinks</h3>
  <a href="#">How it works</a><a href="#">Emloyers</a><a href="#">Professionals</a><a href="#">Join Us</a>
</div>
<div class="abs footer-col" style="left:380px; top:1028px">
  <h3>Resources</h3>
  <a href="#">Term of Use</a><a href="#">Support</a><a href="#">Privacy Policy</a><a href="#">Contact Us</a>
</div>
<div class="abs footer-col" style="left:515px; top:1028px">
  <h3>Follow Us</h3>
</div>
<a class="abs social" href="#" aria-label="Social link" style="left:516px"></a>
<a class="abs social" href="#" aria-label="Social link" style="left:547px"></a>
<a class="abs social" href="#" aria-label="Social link" style="left:578px"></a>
<a class="abs social" href="#" aria-label="Social link" style="left:608px"></a>
<div class="abs footer-brand">TRAVENOK</div>
<p class="abs copyright">© 2016 Company Name &nbsp;All right reserved</p>

</body>
</html>
```